Simple and Clean business card design

We would like the design to be simple clean and to incorporate our colors.

We are open to your design and talent, we have the dots in our logo as we think of it as data points and we connect data points for people.

We are open to see the great creative and clean design you bring to the table

Contact Information for Business Card

please include: name, position, email, phone and website

Font styles to use
Sans Serif

Requirements
Must have
• my colors incorporated, simplicity
Nice to have
• lots of white space, simplicity
Should not have
• complexicity/ complex art

```html
<!DOCTYPE html>
<html lang="en">
<head>
<meta charset="utf-8">
<title>Ambrel Business Card</title>
<link href="https://fonts.googleapis.com/css2?family=Lato:wght@700&family=Arimo:wght@400&display=swap" rel="stylesheet">
<style>
  :root {
    --backdrop: #1c1c1c;
    --kraft-light: #dcb98e;
    --kraft-mid: #c79f6d;
    --kraft-dark: #a9774a;
    --ink: #111111;
    --rule: #3a2a1a;
    --dot-green: #34a853;
  }
  * { margin: 0; padding: 0; box-sizing: border-box; }
  html, body {
    width: 1093px;
    height: 1200px;
    overflow: hidden;
    background: var(--backdrop);
  }
  .canvas {
    position: relative;
    width: 1093px;
    height: 1200px;
  }
  .card {
    position: absolute;
    left: 264px;
    width: 580px;
    height: 357px;
    background: linear-gradient(135deg, var(--kraft-light) 0%, var(--kraft-mid) 55%, var(--kraft-dark) 100%);
    color: var(--ink);
    text-align: center;
  }
  .card--front { top: 226px; }
  .card--back { top: 620px; }

  .person-name {
    position: absolute;
    top: 82px;
    left: 0; right: 0;
    font-family: 'Lato', sans-serif;
    font-weight: 700;
    font-size: 30px;
    letter-spacing: -0.3px;
    line-height: 1;
  }
  .person-role {
    position: absolute;
    top: 118px;
    left: 0; right: 0;
    font-family: 'Arimo', sans-serif;
    font-size: 19px;
    line-height: 1;
  }
  .contact-icons {
    position: absolute;
    top: 157px;
    left: 0; right: 0;
    display: flex;
    justify-content: center;
    align-items: center;
    gap: 6px;
  }
  .contact-icons .rule {
    width: 23px;
    height: 1px;
    background: var(--rule);
    margin: 0 2px;
  }
  .contact-icons svg { width: 26px; height: 26px; display: block; }
  .contact-list {
    position: absolute;
    top: 194px;
    left: 0; right: 0;
    list-style: none;
    font-family: 'Arimo', sans-serif;
    font-size: 19px;
    line-height: 27px;
  }

  .brand {
    position: absolute;
    top: 50%;
    left: 50%;
    transform: translate(-50%, -50%);
    display: flex;
    align-items: center;
    gap: 12px;
  }
  .brand-dot {
    width: 30px;
    height: 30px;
    border-radius: 50%;
    background: var(--dot-green);
  }
  .brand-name {
    font-family: 'Lato', sans-serif;
    font-weight: 700;
    font-size: 72px;
    line-height: 1;
    color: var(--ink);
  }
</style>
</head>
<body>
<main class="canvas">
  <section class="card card--front" aria-label="Card front">
    <h1 class="person-name">NOLAN REYES</h1>
    <p class="person-role">Founder/ CEO</p>
    <div class="contact-icons" aria-hidden="true">
      <span class="rule"></span>
      <svg viewBox="0 0 26 26" fill="none" stroke="#111" stroke-width="2">
        <circle cx="13" cy="13" r="11.5"/>
        <path d="M8.5 8 l2.5-1 2 3.5-1.5 1.3 a7 7 0 0 0 3 3 l1.3-1.5 3.5 2-1 2.5 c-5 1-10.5-4.5-9.8-9.8z" fill="#111" stroke-width="0.8"/>
      </svg>
      <svg viewBox="0 0 26 26" fill="none" stroke="#111" stroke-width="2">
        <circle cx="13" cy="13" r="11.5"/>
        <rect x="7" y="9" width="12" height="8.5" fill="#111" stroke="none"/>
        <path d="M7.5 9.5 l5.5 4.5 5.5-4.5" stroke="#c9a06f" stroke-width="1.2"/>
      </svg>
      <svg viewBox="0 0 26 26" fill="none" stroke="#111" stroke-width="2">
        <circle cx="13" cy="13" r="11.5"/>
        <g stroke-width="1.1">
          <circle cx="13" cy="13" r="6.5"/>
          <ellipse cx="13" cy="13" rx="3" ry="6.5"/>
          <path d="M6.5 13h13M7.5 10h11M7.5 16h11M13 6.5v13"/>
        </g>
      </svg>
      <span class="rule"></span>
    </div>
    <ul class="contact-list">
      <li>555-214-0198</li>
      <li>nolan.reyes@ambrel.one</li>
      <li>www.Ambrel.one</li>
    </ul>
  </section>

  <section class="card card--back" aria-label="Card back">
    <div class="brand">
      <span class="brand-dot" aria-hidden="true"></span>
      <span class="brand-name">Ambrel</span>
    </div>
  </section>
</main>
</body>
</html>
```